Salon and Spa Distributor Business Card

Need a business card. We are are distributor in the salon and spa industry. We identify with natural beauty. Need a card with:
Company Name: Petal Quarry"
Title: "President & CEO"
Address
Company Phone number
email
website
Tag Line:" The Professional Salon Source"

Industry/Entity Type

Business

Contact Information for Business Card

Name: Dov Strommen
Title: "President & CEO"
Address: 31 Harlow Ln, Bexmoor, NJ 07813
Company Phone number: 800-463-5918
email: dovstrommen@petalquarry.example
website: www.petalquarry.example

Requirements
Should not have
• No black backgrounds

```html
<!DOCTYPE html>
<html lang="en">
<head>
<meta charset="utf-8">
<title>Petal Quarry – Business Card</title>
<link rel="stylesheet" href="https://fonts.googleapis.com/css2?family=Questrial&display=swap">
<style>
  :root {
    --green-dark: #2a8a36;
    --green-mid: #4fa53a;
    --green-light: #6cb52f;
    --green-bright: #8cc63f;
    --paper: #ffffff;
    --text-green: #2e8b3a;
    --font-main: "Questrial", "Century Gothic", sans-serif;
  }
  * { box-sizing: border-box; margin: 0; padding: 0; }
  html, body {
    width: 1200px;
    height: 360px;
    overflow: hidden;
    background: var(--paper);
  }
  .sheet {
    display: flex;
    width: 1200px;
    height: 360px;
    font-family: var(--font-main);
  }
  .card {
    position: relative;
    width: 600px;
    height: 360px;
    overflow: hidden;
    background: var(--paper);
  }
  .card-art {
    position: absolute;
    inset: 0;
    width: 600px;
    height: 360px;
  }

  /* Front */
  .brand {
    position: absolute;
    left: 172px;
    top: 24px;
    width: 360px;
    text-align: center;
    color: var(--green-light);
    white-space: nowrap;
  }
  .brand-name {
    font-size: 35px;
    line-height: 1;
    font-weight: 400;
  }
  .brand-tagline {
    font-size: 18.5px;
    line-height: 1.2;
    margin-top: 6px;
  }
  .person {
    position: absolute;
    left: 150px;
    top: 132px;
    width: 400px;
    text-align: center;
    color: var(--text-green);
    white-space: nowrap;
  }
  .person-name {
    font-size: 47px;
    line-height: 1;
    font-weight: 400;
  }
  .person-title {
    font-size: 27px;
    line-height: 1.1;
    margin-top: 8px;
  }
  .leaf-art {
    position: absolute;
    left: 0;
    top: 228px;
    width: 130px;
    height: 132px;
    background: radial-gradient(circle at 40% 55%, rgba(140,198,63,.55), rgba(108,181,47,.12) 65%, transparent 72%);
  }
  .contact {
    position: absolute;
    left: 104px;
    top: 306px;
    width: 490px;
    text-align: center;
    color: var(--paper);
    font-size: 15px;
    line-height: 22px;
    font-style: normal;
    white-space: nowrap;
  }
  .contact .sep { margin: 0 6px; }

  /* Back */
  .hair-art {
    position: absolute;
    left: 0;
    top: 0;
    width: 600px;
    height: 300px;
    background:
      radial-gradient(ellipse 58% 75% at 60% 45%, rgba(79,165,58,.85), rgba(108,181,47,.45) 55%, rgba(255,255,255,0) 80%);
  }
  .web-address {
    position: absolute;
    left: 0;
    right: 0;
    top: 300px;
    text-align: center;
    font-size: 44px;
    line-height: 1;
    color: var(--paper);
    -webkit-text-stroke: 2px var(--green-dark);
    letter-spacing: 0.5px;
    white-space: nowrap;
  }
</style>
</head>
<body>
<main class="sheet">

  <section class="card card-front" aria-label="Card front">
    <svg class="card-art" viewBox="0 0 600 360" aria-hidden="true">
      <rect width="600" height="360" fill="var(--green-light)"/>
      <path d="M0 226 C150 300 420 300 600 268 V360 H0Z" fill="var(--green-dark)"/>
      <path d="M0 168 C120 262 380 292 600 196" fill="none" stroke="var(--paper)" stroke-width="5"/>
      <ellipse cx="320" cy="78" rx="362" ry="156" fill="var(--paper)"/>
      <path d="M470 0 C560 52 600 130 600 218 V0Z" fill="var(--green-bright)"/>
      <path d="M520 0 C575 45 600 100 600 150 V0Z" fill="var(--green-mid)" opacity=".7"/>
    </svg>
    <div class="leaf-art" role="img" aria-label="Decorative green leaves"></div>

    <header class="brand">
      <h1 class="brand-name">Petal Quarry</h1>
      <p class="brand-tagline">The Professional Salon Source</p>
    </header>

    <div class="person">
      <h2 class="person-name">Dov Strommen</h2>
      <p class="person-title">President &amp; CEO</p>
    </div>

    <address class="contact">
      <div>31 Harlow Ln, Bexmoor, NJ 07813<span class="sep">·</span>800-463-5918</div>
      <div>dovstrommen@petalquarry.example<span class="sep">·</span>www.petalquarry.example</div>
    </address>
  </section>

  <section class="card card-back" aria-label="Card back">
    <div class="hair-art" role="img" aria-label="Large green illustration of flowing hair and leaves"></div>
    <p class="web-address">www.petalquarry.example</p>
  </section>

</main>
</body>
</html>
```